Professional violinist needs business cards

I am trying to attract the following jobs:
-private violin lessons (primarily classical)
-performance gigs (weddings, birthday parties, funerals, etc.)
-collaborations with other artists (studio recordings, performances)

I want to communicate that I have a very high standard of excellence for my work, but I also love people and celebrations.
Values/style words I like are:
love, joy, peace, fun, beauty, authenticity, excellence, warmth, refined/sleek, free spirited. If that's too confusing, just ignore :)

I will attach my favorite business card template that I could find on Canva. The lines are supposed to be like a music staff, which I think is really cool, but I also don't want it to look too busy. I like the simple black and white--I think it looks sharp--but I also am open to other ideas. I also have seen business cards with pictures included that looked great, so I attached an image that could be used as well.

I am also attaching a file that I made of my initials that could be used as a logo, but I'm not sure if it should be included.

Information on the card:
-My name (18 letters total)
-"violinist"
-phone number, email, website

Thank you!

```html
<!DOCTYPE html>
<html lang="en">
<head>
<meta charset="utf-8">
<title>Juliette Harwood – Violinist Business Cards</title>
<link rel="stylesheet" href="https://fonts.googleapis.com/css2?family=Dancing+Script:wght@500&family=Cinzel:wght@500&family=Crimson+Text&display=swap">
<style>
  :root {
    --backdrop: #2b2b2b;
    --card: #22262a;
    --card-edge: #1c1f22;
    --staff: #3c4146;
    --gold: #cdb690;
    --gold-deep: #a88a58;
    --gold-light: #e3d2b3;
    --ink-light: #e6e2dc;
    --ink-dark: #1e2125;
    --photo-stone: #7a7160;
    --photo-shadow: #3a352d;
  }
  * { margin: 0; padding: 0; box-sizing: border-box; }
  html, body { width: 1200px; height: 1138px; overflow: hidden; }
  body { background: var(--backdrop); position: relative; }

  .card {
    position: absolute;
    width: 620px;
    height: 375px;
    border-radius: 14px;
    background: var(--card);
    overflow: hidden;
    box-shadow: 0 4px 12px rgba(0,0,0,.45);
  }
  .card--front { left: 274px; top: 186px; }
  .card--back  { left: 276px; top: 608px; }

  /* front */
  .staff { position: absolute; left: 0; right: 0; top: 93px; }
  .staff__line { height: 1px; background: var(--staff); margin-bottom: 22px; }
  .monogram {
    position: absolute; left: 0; right: 0; top: 88px;
    text-align: center;
    font-family: "Dancing Script", cursive;
    font-weight: 500;
    font-size: 78px;
    color: var(--gold);
    line-height: 1;
  }
  .front__name {
    position: absolute; left: 0; right: 0; top: 200px;
    text-align: center;
    font-family: "Dancing Script", cursive;
    font-size: 38px;
    color: var(--ink-light);
  }
  .front__role {
    position: absolute; left: 0; right: 0; top: 256px;
    text-align: center;
    font-family: "Cinzel", serif;
    font-size: 18px;
    letter-spacing: 3px;
    color: var(--ink-light);
  }

  /* back */
  .portrait {
    position: absolute; left: 372px; top: 60px; width: 248px; height: 315px;
    background:
      linear-gradient(90deg, var(--card) 0%, rgba(34,38,42,0) 28%),
      radial-gradient(ellipse at 55% 70%, #2a2624 0%, rgba(42,38,36,0) 40%),
      linear-gradient(160deg, var(--photo-stone), var(--photo-shadow));
  }
  .waves { position: absolute; left: 0; top: 0; }
  .back__tag {
    position: absolute; right: 42px; top: 22px;
    text-align: center;
    font-family: "Dancing Script", cursive;
    font-size: 23px;
    line-height: 1.4;
    color: var(--ink-dark);
  }
  .brand { position: absolute; left: 30px; top: 130px; display: flex; align-items: center; }
  .brand__mark {
    font-family: "Dancing Script", cursive;
    font-size: 44px;
    color: var(--gold);
    margin-right: 14px;
    line-height: 1;
  }
  .brand__name {
    font-family: "Dancing Script", cursive;
    font-size: 25px;
    color: var(--ink-light);
    line-height: 1.1;
  }
  .brand__role {
    display: flex; align-items: center; justify-content: center; gap: 10px;
    font-family: "Cinzel", serif;
    font-size: 11px;
    letter-spacing: 2px;
    color: var(--ink-light);
    margin-top: 2px;
  }
  .brand__role::before, .brand__role::after {
    content: ""; width: 44px; height: 1px; background: var(--ink-light); opacity: .6;
  }
  .contacts { position: absolute; left: 30px; top: 240px; list-style: none; }
  .contacts__item {
    display: flex; align-items: center; height: 23.5px;
    font-family: "Crimson Text", serif;
    font-size: 15px;
    color: var(--ink-light);
  }
  .contacts__icon { width: 14px; height: 14px; margin-right: 16px; fill: var(--ink-light); }
  .contacts__accent { color: var(--gold); }
</style>
</head>
<body>

<section class="card card--front">
  <div class="staff">
    <div class="staff__line"></div>
    <div class="staff__line"></div>
    <div class="staff__line"></div>
    <div class="staff__line"></div>
  </div>
  <div class="monogram">JH</div>
  <div class="front__name">Juliette Harwood</div>
  <div class="front__role">VIOLINIST</div>
</section>

<section class="card card--back">
  <div class="portrait" role="img" aria-label="Photo of the violinist holding her violin in front of a stone wall"></div>

  <svg class="waves" width="620" height="375" viewBox="0 0 620 375">
    <defs>
      <linearGradient id="goldFill" x1="0" y1="0" x2="1" y2="0">
        <stop offset="0" stop-color="#e0ccaa"/>
        <stop offset=".5" stop-color="#c9ad7e"/>
        <stop offset="1" stop-color="#b8965f"/>
      </linearGradient>
    </defs>
    <path d="M0,0 H620 V120 C540,134 470,126 390,90 C300,50 240,30 150,30 C90,30 40,40 0,55 Z" fill="url(#goldFill)"/>
    <path d="M0,60 C60,20 170,8 240,30 C300,48 340,72 400,92 C470,116 540,122 620,112 V100 C540,108 470,100 400,74 C330,48 280,20 210,14 C130,8 60,28 0,48 Z" fill="var(--card)"/>
    <path d="M0,72 C80,40 200,38 280,62 C340,80 380,108 440,122 C510,138 570,134 620,124 V134 C560,148 500,148 430,134 C370,120 330,96 270,76 C190,52 90,56 0,86 Z" fill="var(--card)"/>
    <path d="M40,72 C120,50 220,50 300,78 C360,98 400,118 460,130 C520,142 580,138 620,128" fill="none" stroke="var(--gold-light)" stroke-width="1.5"/>
  </svg>

  <div class="back__tag">Juliette<br>Harwood</div>

  <div class="brand">
    <div class="brand__mark">JH</div>
    <div>
      <div class="brand__name">Juliette Harwood</div>
      <div class="brand__role">VIOLINIST</div>
    </div>
  </div>

  <ul class="contacts">
    <li class="contacts__item">
      <svg class="contacts__icon" viewBox="0 0 16 16"><path d="M1 5c0-2 2-3 7-3s7 1 7 3v1h-3V5H4v1H1zM3 7h10l2 7H1z"/></svg>
      +1 (202) 555-0147
    </li>
    <li class="contacts__item">
      <svg class="contacts__icon" viewBox="0 0 16 16"><path d="M8 1a5 5 0 0 0-5 5c0 4 5 9 5 9s5-5 5-9a5 5 0 0 0-5-5zm0 7a2 2 0 1 1 0-4 2 2 0 0 1 0 4z"/></svg>
      Arlington, VA
    </li>
    <li class="contacts__item">
      <svg class="contacts__icon" viewBox="0 0 16 16"><circle cx="8" cy="8" r="6.5" fill="none" stroke="#e6e2dc" stroke-width="1.2"/><path d="M1.5 8h13M8 1.5c-3 3-3 10 0 13M8 1.5c3 3 3 10 0 13" fill="none" stroke="#e6e2dc" stroke-width="1"/></svg>
      www.<span class="contacts__accent">JulietteHarwood</span>.com
    </li>
    <li class="contacts__item">
      <svg class="contacts__icon" viewBox="0 0 16 16"><path d="M1 3h14v10H1zM2 4l6 5 6-5" fill="none" stroke="#e6e2dc" stroke-width="1.3"/></svg>
      Juliette@JulietteHarwood.com
    </li>
  </ul>
</section>

</body>
</html>
```